Brightlane Rapid Rinse Web Design

We are looking for a web design that highlights our state of the art fully automated commercial vehicle washing equipment. Similar system to a car wash however this system is meant for the largest vehicles on our roadways. Transport trucks with or without a trailer, busses both highway and school, RV's from 5th wheel type to A Class. Cement trucks, dump trucks, vac trucks, fuel trucks etc. Pick ups with utility trailers...Refrigerator truck clean outs.
Brightlane Rapid Rinse will wash your vehicle quickly and with a minimal impact on the environment

Home page
About us
Why Brightlane
Services and pricing
Videos of wash system
Fleets
contact us

Target Market(s)

Commercial vehicle owners and operators as well as corporate fleets. Includes busses, municipal, school and highway.both school and

Industry/Entity Type

transportation

Coding

Coded - Design and coding required

Number of Pages Required

5+ page

Font styles to use
Sans Serif

Colors
0054AA
0677BA
7BADD7
CADEEF
E8F1F8

Requirements
Must have
• Welcome page,why us page which describes the financial and environmental benefits. payment processing page, contact us page, Services which is washing vehicles and greasing for commercial vehicles that want that service and grease
Nice to have
• pictures of both clean and dirty commercial vehicles ie. before and after

```html
<!DOCTYPE html>
<html lang="en">
<head>
<meta charset="utf-8">
<title>Brightlane Rapid Rinse</title>
<link rel="stylesheet" href="https://fonts.googleapis.com/css2?family=Poppins:wght@400;500;600;700&family=Arimo:wght@400;700&display=swap">
<style>
:root{
  --blue:#0054AA;--blue2:#0677BA;--sky:#7BADD7;--pale:#CADEEF;--mist:#E8F1F8;
  --ink:#1a1a1a;--text:#333;--white:#fff;--foot:#0d0d0d;
}
*{margin:0;padding:0;box-sizing:border-box}
html,body{width:1200px;height:4099px;overflow:hidden}
body{position:relative;font-family:Arimo,Arial,sans-serif;color:var(--text);background:#fff}
.abs{position:absolute}
.head{font-family:Poppins,Arial,sans-serif}
section,header,footer{position:absolute;left:0;width:1200px}
.center{left:0;width:1200px;text-align:center}
.rule{position:absolute;height:3px;width:52px;left:574px;background:var(--blue)}
.rule.white{background:#fff}
/* header */
.topbar{top:0;height:86px;background:var(--blue)}
.brand{left:102px;top:14px;color:#fff;font-family:Poppins,sans-serif;font-weight:600;font-size:21px;line-height:26px;text-align:center}
.brand small{display:block;font-size:16px;font-weight:500}
.nav{right:99px;top:21px;display:flex;align-items:center;gap:0;font-family:Poppins,sans-serif;font-size:16px;color:#fff;font-weight:500}
.nav span{margin-right:22px}
.nav .cta{background:#fff;color:var(--blue);padding:0 12px;height:43px;line-height:43px;font-weight:600;margin:0}
/* hero */
.hero{top:86px;height:600px;background:linear-gradient(100deg,#2a3440 0%,#4b5867 45%,#8c96a0 70%,#5e6670 100%)}
.hero h1{position:absolute;left:99px;top:150px;font-family:Poppins,sans-serif;font-weight:700;font-size:48px;line-height:57px;color:#fff}
.hero p{position:absolute;left:99px;top:280px;font-family:Poppins,sans-serif;font-size:19px;color:#fff}
.btn{position:absolute;height:43px;line-height:41px;font-family:Poppins,sans-serif;font-weight:600;font-size:16px;text-align:center}
.btn.solid{left:100px;top:339px;width:137px;background:#fff;color:var(--blue)}
.btn.ghost{left:250px;top:339px;width:140px;border:2px solid #fff;color:#fff}
.arrow{position:absolute;width:28px;height:28px}
/* services */
.services{top:686px;height:721px;background:#fff}
.h2{font-family:Poppins,sans-serif;font-weight:600;font-size:32px;color:var(--ink)}
.lead{font-size:15px;color:#333}
.card{position:absolute;top:226px;width:312px;text-align:center}
.card .ph{height:234px}
.card h3{font-family:Poppins,sans-serif;font-weight:500;font-size:19px;color:var(--ink);margin-top:28px}
.card p{font-size:14px;line-height:29px;margin-top:6px;padding:0 12px}
/* mission */
.mission{top:1407px;height:633px;background:linear-gradient(120deg,#0054AA 0%,#0a5fb4 50%,#0054AA 100%)}
.mission h2{position:absolute;left:99px;top:80px;font-family:Poppins,sans-serif;font-weight:600;font-size:32px;color:#fff}
.mission .rule{left:99px;top:135px}
.mission .para{position:absolute;left:99px;top:156px;width:460px;font-size:14.5px;line-height:29px;color:#fff}
.feat{position:absolute;left:99px;display:flex;align-items:center;gap:17px;color:#fff;font-family:Poppins,sans-serif;font-weight:600;font-size:17px}
.feat .ic{width:67px;height:67px;border:2px solid #fff;border-radius:50%;display:flex;align-items:center;justify-content:center}
.frame{position:absolute;left:678px;top:71px;width:428px;height:380px;background:#2f6fbb;opacity:.75}
/* before after */
.ba{top:2040px;height:670px;background:#f1f6fb}
.ba h2{font-weight:500}
.ba .cap{position:absolute;top:584px;width:487px;text-align:center;font-family:Poppins,sans-serif;font-size:20px;color:var(--ink)}
/* contact */
.contact{top:2710px;height:428px;background:linear-gradient(120deg,#0677BA,#0a6fb5 60%,#0677BA)}
.contact .h2{color:#fff}
.contact .lead{color:#fff;line-height:30px}
.citem{position:absolute;top:213px;display:flex;align-items:center;gap:16px;color:#fff;font-size:15px}
.citem .ic{width:45px;height:45px;border:2px solid #fff;border-radius:50%;display:flex;align-items:center;justify-content:center}
.btn.light{left:533px;top:290px;width:134px;background:#fff;color:var(--blue)}
/* testimonials */
.testi{top:3138px;height:535px;background:#fff}
.tcard{position:absolute;top:209px;width:311px;height:191px;border-top:3px solid var(--blue);border-radius:10px;background:#fff;box-shadow:0 4px 18px rgba(0,0,0,.1);text-align:center}
.tcard p{font-size:14px;line-height:25.5px;color:#555;padding:64px 22px 0}
.tcard .av{position:absolute;left:111px;top:-46px;width:89px;height:89px;border-radius:50%;background:linear-gradient(#c9d3dc,#8a96a3);border:3px solid #fff}
.tcard .badge{position:absolute;left:171px;top:18px;width:26px;height:26px;border-radius:50%;background:#fff;border:2px solid #d9dde2}
.tcard .tip{position:absolute;left:146px;bottom:-10px;width:20px;height:20px;background:#fff;transform:rotate(45deg);box-shadow:4px 4px 6px rgba(0,0,0,.06)}
.who{position:absolute;top:429px;width:311px;text-align:center;font-size:14px;color:#111}
.who b{font-weight:400;margin-right:18px}
.who i{font-style:normal;color:#f3c10f;letter-spacing:1px}
/* footer */
.footer{top:3673px;height:426px;background:var(--foot);color:#fff}
.footer h4{position:absolute;top:60px;font-family:Poppins,sans-serif;font-weight:500;font-size:20px}
.links{position:absolute;top:95px;list-style:none;font-size:15px}
.links li{height:31px;display:flex;align-items:center;gap:10px}
.fcon{position:absolute;left:519px;display:flex;align-items:center;gap:12px;font-size:15px}
.fcon .ic{width:38px;height:38px;border-radius:50%;background:var(--blue);display:flex;align-items:center;justify-content:center}
.social{position:absolute;top:382px;width:25px;height:25px;border-radius:50%;background:var(--blue)}
</style>
</head>
<body>

<header class="topbar">
  <div class="abs brand">Brightlane Rapid<small>Rinse</small></div>
  <nav class="abs nav">
    <span>Home</span><span>About us</span><span>Services and pricing</span><span>Videos</span><span>More ▾</span><span class="cta">Contact Us</span>
  </nav>
</header>

<section class="hero" role="img" aria-label="Photo of a white tanker truck being sprayed down on a wet wash pad">
  <h1>Brightlane Rapid<br>Rinse</h1>
  <p>Speed (less than 15 minutes)</p>
  <div class="btn solid">Book a Wash</div>
  <div class="btn ghost">Learn More</div>
  <svg class="arrow" style="left:26px;top:286px" viewBox="0 0 28 28"><circle cx="14" cy="14" r="13" fill="none" stroke="#fff" stroke-width="1.5"/><path d="M16 9l-5 5 5 5" fill="none" stroke="#fff" stroke-width="1.5"/></svg>
  <svg class="arrow" style="left:1127px;top:286px" viewBox="0 0 28 28"><circle cx="14" cy="14" r="13" fill="none" stroke="#fff" stroke-width="1.5"/><path d="M12 9l5 5-5 5" fill="none" stroke="#fff" stroke-width="1.5"/></svg>
</section>

<section class="services">
  <div class="abs center h2" style="top:83px">Our Services</div>
  <div class="rule" style="top:141px"></div>
  <div class="abs center lead" style="top:169px">Lorem ipsum dolor sit amet, consectetur adipiscing elit, sed do eiusmod tempor incididunt ut labore et dolore magna aliqua.</div>
  <div class="card" style="left:99px">
    <div class="ph" role="img" aria-label="Photo of a truck inside an automated wash bay with red and black brushes" style="background:linear-gradient(180deg,#9aa3ab,#c8ccd0 60%,#7d858c)"></div>
    <h3>Automated Truck Wash</h3>
    <p>Lorem ipsum dolor sit amet, consectetur adipiscing elit, sed do eiusmod tempor incididunt ut labore et dolore magna aliqua.</p>
  </div>
  <div class="card" style="left:443px">
    <div class="ph" role="img" aria-label="Photo of an orange vacuum truck" style="background:linear-gradient(180deg,#9aa29c,#b8672e 55%,#6e5a48)"></div>
    <h3>Additional Services</h3>
    <p>Lorem ipsum dolor sit amet, consectetur adipiscing elit, sed do eiusmod tempor incididunt ut labore et dolore magna aliqua.</p>
  </div>
  <div class="card" style="left:788px">
    <div class="ph" role="img" aria-label="Photo of a row of white fleet trucks parked under a sunset sky" style="background:linear-gradient(180deg,#7e9ab8,#c9c3b4 50%,#5c6470)"></div>
    <h3>Fleet Services</h3>
    <p>Lorem ipsum dolor sit amet, consectetur adipiscing elit, sed do eiusmod tempor incididunt ut labore et dolore magna aliqua.</p>
  </div>
</section>

<section class="mission">
  <h2>Our Mission</h2>
  <div class="rule white"></div>
  <p class="para">Lorem ipsum dolor sit amet, consectetur adipiscing elit, sed do eiusmod tempor incididunt ut labore et dolore magna aliqua. Ut enim ad minim veniam, nisi ut aliquip ex ea commodo consequat.</p>
  <div class="feat" style="top:265px"><div class="ic"><svg width="34" height="26" viewBox="0 0 34 26" fill="none" stroke="#fff" stroke-width="1.6"><rect x="2" y="4" width="20" height="14"/><path d="M22 8h6l4 5v5h-10z"/><circle cx="8" cy="20" r="3"/><circle cx="26" cy="20" r="3"/></svg></div>Truck Washing</div>
  <div class="feat" style="top:354px"><div class="ic"><svg width="28" height="30" viewBox="0 0 28 30" fill="none" stroke="#fff" stroke-width="1.6"><rect x="5" y="3" width="18" height="24" rx="2"/><path d="M10 10h8M10 15h8M10 20h5"/></svg></div>Advanced Technology</div>
  <div class="feat" style="top:444px"><div class="ic"><svg width="30" height="30" viewBox="0 0 30 30" fill="none" stroke="#fff" stroke-width="1.6"><circle cx="15" cy="15" r="11"/><path d="M4 15h22M15 4c-5 5-5 17 0 22M15 4c5 5 5 17 0 22"/></svg></div>Sustainable Practices</div>
  <div class="frame"></div>
  <div class="abs" role="img" aria-label="Photo of a yellow dump truck being pressure washed at a hillside quarry" style="left:635px;top:102px;width:441px;height:423px;background:linear-gradient(180deg,#8d8c72,#a79d7c 50%,#c2a12f 70%,#8a7d66)"></div>
</section>

<section class="ba">
  <div class="abs center h2" style="top:66px">Before/After</div>
  <div class="rule" style="top:116px"></div>
  <div class="abs" role="img" aria-label="Photo of a dirty orange garbage truck before washing" style="left:102px;top:145px;width:487px;height:398px;background:linear-gradient(160deg,#8b8f92,#b56a3a 45%,#6f5544)"></div>
  <div class="abs" role="img" aria-label="Photo of the same orange garbage truck clean after washing" style="left:614px;top:145px;width:487px;height:398px;background:linear-gradient(160deg,#c7cbce,#e0662a 50%,#4a4c50)"></div>
  <div class="cap" style="left:102px">Before Truck</div>
  <div class="cap" style="left:614px">After Truck</div>
  <svg class="arrow" style="left:51px;top:336px" viewBox="0 0 28 28"><circle cx="14" cy="14" r="13" fill="none" stroke="#222" stroke-width="1.3"/><path d="M16 9l-5 5 5 5" fill="none" stroke="#222" stroke-width="1.5"/></svg>
  <svg class="arrow" style="left:1119px;top:336px" viewBox="0 0 28 28"><circle cx="14" cy="14" r="13" fill="none" stroke="#222" stroke-width="1.3"/><path d="M12 9l5 5-5 5" fill="none" stroke="#222" stroke-width="1.5"/></svg>
</section>

<section class="contact">
  <div class="abs center h2" style="top:64px">Contact US</div>
  <div class="rule white" style="top:116px"></div>
  <div class="abs lead" style="left:130px;top:132px;width:940px;text-align:center">Lorem ipsum dolor sit amet, consectetur adipiscing elit, sed do eiusmod tempor incididunt ut labore et dolore magna aliqua. Ut enim ad minim veniam, quis nostrud exercitation ullamco laboris nisi ut aliquip ex ea commodo consequat.</div>
  <div class="citem" style="left:99px"><div class="ic"><svg width="18" height="18" viewBox="0 0 24 24" fill="#fff"><path d="M6.6 10.8a15 15 0 006.6 6.6l2.2-2.2c.3-.3.7-.4 1-.2 1.1.4 2.3.6 3.6.6.6 0 1 .4 1 1V20c0 .6-.4 1-1 1C10.6 21 3 13.4 3 4c0-.6.4-1 1-1h3.5c.6 0 1 .4 1 1 0 1.3.2 2.5.6 3.6.1.3 0 .7-.2 1z"/></svg></div>+1 555 0142 7788</div>
  <div class="citem" style="left:372px"><div class="ic"><svg width="18" height="14" viewBox="0 0 24 18" fill="#fff"><path d="M0 0h24v2L12 10 0 2z"/><path d="M0 5l12 8 12-8v13H0z"/></svg></div>info@brightlanerapidrinse</div>
  <div class="citem" style="left:748px"><div class="ic"><svg width="16" height="20" viewBox="0 0 16 22" fill="none" stroke="#fff" stroke-width="2"><path d="M8 21s7-7 7-12A7 7 0 001 9c0 5 7 12 7 12z"/><circle cx="8" cy="9" r="2.5"/></svg></div>Brightlane Rapid Rinse,United State.</div>
  <div class="btn light">Contact Us</div>
</section>

<section class="testi">
  <div class="abs center h2" style="top:88px">Customer Testimonials</div>
  <div class="rule" style="top:138px;width:64px;left:568px"></div>
  <div class="tcard" style="left:111px"><div class="av" role="img" aria-label="Customer portrait"></div><div class="badge"></div><p>Sed ut perspiciatis unde omnis iste natus error sit voluptatem accusantium doloremque laudantium, totam rem aperiam, eaque ipsa</p><div class="tip"></div></div>
  <div class="tcard" style="left:445px"><div class="av" role="img" aria-label="Customer portrait"></div><div class="badge"></div><p>Sed ut perspiciatis unde omnis iste natus error sit voluptatem accusantium doloremque laudantium, totam rem aperiam, eaque ipsa</p><div class="tip"></div></div>
  <div class="tcard" style="left:778px"><div class="av" role="img" aria-label="Customer portrait"></div><div class="badge"></div><p>Sed ut perspiciatis unde omnis iste natus error sit voluptatem accusantium doloremque laudantium, totam rem aperiam, eaque ipsa</p><div class="tip"></div></div>
  <div class="who" style="left:111px"><b>Sam Rivers</b><i>★★★★★</i></div>
  <div class="who" style="left:445px"><b>Sam Rivers</b><i>★★★★★</i></div>
  <div class="who" style="left:778px"><b>Sam Rivers</b><i>★★★★★</i></div>
</section>

<footer class="footer">
  <h4 style="left:97px">Quick Links</h4>
  <h4 style="left:323px">Other Links</h4>
  <h4 style="left:519px">Contact Us</h4>
  <h4 style="left:828px">Sign Up To Our Newsletter</h4>
  <ul class="links" style="left:97px">
    <li>➔ Home p</li><li>➔ About us</li><li>➔ Services and pricing</li><li>➔ Videos</li><li>➔ Fleets</li><li>➔ contact us</li>
  </ul>
  <ul class="links" style="left:323px">
    <li>➔ FAQ</li><li>➔ Tems of Use</li><li>➔ Privacy Policy</li><li>➔ Support Links</li><li>➔ Conditions</li>
  </ul>
  <div class="fcon" style="top:108px"><div class="ic"><svg width="12" height="16" viewBox="0 0 16 22" fill="#fff"><path d="M8 21s7-7 7-12A7 7 0 001 9c0 5 7 12 7 12z"/></svg></div>Company Name,United State.</div>
  <div class="fcon" style="top:168px"><div class="ic"><svg width="14" height="11" viewBox="0 0 24 18" fill="#fff"><path d="M0 0h24v2L12 10 0 2z"/><path d="M0 5l12 8 12-8v13H0z"/></svg></div>hello@brightlanerinse.com</div>
  <div class="fcon" style="top:228px"><div class="ic"><svg width="14" height="14" viewBox="0 0 24 24" fill="#fff"><path d="M6.6 10.8a15 15 0 006.6 6.6l2.2-2.2c.3-.3.7-.4 1-.2 1.1.4 2.3.6 3.6.6.6 0 1 .4 1 1V20c0 .6-.4 1-1 1C10.6 21 3 13.4 3 4c0-.6.4-1 1-1h3.5c.6 0 1 .4 1 1 0 1.3.2 2.5.6 3.6.1.3 0 .7-.2 1z"/></svg></div>+1 555 0142 7788</div>
  <p class="abs" style="left:828px;top:112px;width:275px;font-size:14.5px;line-height:31px">Lorem ipsum dolor sit amet,consectetur adipiscing elit,adipiscing elit.</p>
  <div class="abs" style="left:831px;top:182px;font-size:15px">Email</div>
  <div class="abs" style="left:831px;top:210px;width:270px;height:1px;background:#fff"></div>
  <div class="abs head" style="left:836px;top:242px;width:144px;height:51px;line-height:51px;border-radius:26px;background:var(--blue);text-align:center;font-weight:600;font-size:17px">Subscribe</div>
  <div class="abs" style="left:97px;top:365px;width:1004px;height:1px;background:#555"></div>
  <div class="abs" style="left:97px;top:388px;font-size:15px">Copyrights@2024.Brightlane Rapid Rinse.All Rights Reserved</div>
  <div class="social" style="left:932px"></div>
  <div class="social" style="left:973px"></div>
  <div class="social" style="left:1013px"></div>
  <div class="social" style="left:1053px"></div>
</footer>

</body>
</html>
```